Fern Acupuncture Business Card Design

I would like a business card design for my acupuncture business which is based from 2 practices in Melbourne, Australia.

The front of the card should include:

*The Logo
* Name - Miranda Tesselhoff (B.App.Sc.(TCM), Dip.Rem.Mass.). (I would like the letters after my name in slightly smaller font)
* Mobile number - 0472 318 604
* Web address - www.fernacupuncture.com.au

On the back of the card I would somehow like to fit my 2 clinic addresses in. They are:

The Calm & Balance Rooms
842 Pellam St, Camberwell VIC 3124
Ph: 1300 287 419

Riverbend Natural Therapies & Herbal Practice
19 Quillon Ave, Malvern East VIC 3145
Ph: (03) 9731 4052

If there is space, I'd also like to add to the back of the card - Next Appointment............................ (or something along those lines).

Thanks and happy designing!

Target Market(s)

Health consumers, and colleagues in the health industry

Industry/Entity Type

Clinic

Contact Information for Business Card

as above in brief

Requirements
Must have
• I've seen some ok designs coming in, however I'd like to avoid the generic look with the added curved line details etc. I don't particularly need extra patterns added to the card. I'd prefer it to look quite clean and simple, and using more earthy colours (I'm not super keen on the lime green that a lot of designs seem to include. I don't mind the full black or white look, (obviously the back side needs to be a lighter colour to allow me to write appointment details on it). I also quite like the idea of the background looking like brown recycled paper (just an idea - that's not 100% necessary).
Nice to have
• I have an idea that I could have the main flower part of the logo printed as metallic.
Should not have
• Generic patterns and too much added detail.

```html
<!DOCTYPE html>
<html lang="en">
<head>
<meta charset="utf-8">
<title>Fern Acupuncture – Business Card</title>
<link href="https://fonts.googleapis.com/css2?family=Arimo:wght@400;700&display=swap" rel="stylesheet">
<style>
  :root {
    --stage: #5d6066;
    --card: #eff4d6;
    --ink: #1c1c1c;
    --ink-soft: #3a3a3a;
    --panel: #ffffff;
    --mark: #1b1b1b;
    --rule: #333333;
  }
  * { box-sizing: border-box; margin: 0; padding: 0; }
  html, body {
    width: 1200px; height: 960px; overflow: hidden;
    background: var(--stage);
    font-family: "Arimo", Arial, sans-serif;
    color: var(--ink);
  }
  .stage {
    width: 1200px; height: 960px;
    display: flex; flex-direction: column; align-items: center;
    justify-content: center; gap: 56px;
  }
  .card {
    width: 700px; height: 400px;
    background: var(--card);
    position: relative;
    box-shadow: 0 6px 18px rgba(0,0,0,.35);
  }

  /* Front */
  .card--front {
    display: flex; flex-direction: column; align-items: center;
    justify-content: center; text-align: center;
  }
  .brand { display: flex; flex-direction: column; align-items: center; gap: 10px; margin-bottom: 22px; }
  .brand__dot { width: 96px; height: 96px; border-radius: 50%; background: var(--mark); }
  .brand__name { font-size: 15px; font-weight: 700; letter-spacing: .5px; color: var(--ink); }
  .practitioner__name { font-size: 28px; font-weight: 700; letter-spacing: -.2px; }
  .practitioner__quals { font-size: 13px; font-weight: 700; margin-top: 4px; }
  .contact { margin-top: 26px; display: flex; flex-direction: column; gap: 16px; }
  .contact__phone { font-size: 17px; }
  .contact__web { font-size: 17px; font-weight: 700; }

  /* Back */
  .clinics { position: absolute; left: 40px; top: 36px; display: flex; flex-direction: column; gap: 18px; }
  .clinic__name { font-size: 21px; font-weight: 700; }
  .clinic__address { font-size: 16px; color: var(--ink-soft); margin-top: 4px; }
  .clinic__phone { font-size: 16px; color: var(--ink-soft); margin-top: 3px; display: flex; align-items: center; gap: 8px; }
  .clinic__phone svg { width: 13px; height: 13px; }

  .appointment {
    position: absolute; left: 180px; right: 22px; bottom: 22px; height: 150px;
    background: var(--panel); padding: 22px 30px;
    display: flex; flex-direction: column; gap: 16px;
  }
  .appointment__title { font-size: 19px; }
  .appointment__row { display: flex; align-items: baseline; font-size: 19px; }
  .appointment__fill { flex: 1; border-bottom: 2px dotted var(--rule); margin: 0 4px; }
  .appointment__fill--date { flex: 1.6; }
</style>
</head>
<body>
<main class="stage">
  <section class="card card--front" aria-label="Card front">
    <div class="brand">
      <span class="brand__dot"></span>
      <span class="brand__name">Fern Acupuncture</span>
    </div>
    <div class="practitioner">
      <h1 class="practitioner__name">Miranda Tesselhoff</h1>
      <p class="practitioner__quals">(B.App.Sc.(TCM), Dip.Rem.Mass.)</p>
    </div>
    <div class="contact">
      <p class="contact__phone">0472 318 604</p>
      <p class="contact__web">www.fernacupuncture.com.au</p>
    </div>
  </section>

  <section class="card card--back" aria-label="Card back">
    <div class="clinics">
      <div class="clinic">
        <h2 class="clinic__name">The Calm &amp; Balance Rooms</h2>
        <p class="clinic__address">842 Pellam St, Camberwell VIC 3124</p>
        <p class="clinic__phone"><svg viewBox="0 0 24 24" aria-hidden="true"><path fill="#1c1c1c" d="M6.6 10.8a15.2 15.2 0 0 0 6.6 6.6l2.2-2.2c.3-.3.7-.4 1-.2 1.1.4 2.3.6 3.6.6.6 0 1 .4 1 1V20c0 .6-.4 1-1 1A17 17 0 0 1 3 4c0-.6.4-1 1-1h3.5c.6 0 1 .4 1 1 0 1.3.2 2.5.6 3.6.1.3 0 .7-.2 1z"/></svg>1300 287 419</p>
      </div>
      <div class="clinic">
        <h2 class="clinic__name">Riverbend Natural Therapies &amp; Herbal Practice</h2>
        <p class="clinic__address">19 Quillon Ave, Malvern East VIC 3145</p>
        <p class="clinic__phone"><svg viewBox="0 0 24 24" aria-hidden="true"><path fill="#1c1c1c" d="M6.6 10.8a15.2 15.2 0 0 0 6.6 6.6l2.2-2.2c.3-.3.7-.4 1-.2 1.1.4 2.3.6 3.6.6.6 0 1 .4 1 1V20c0 .6-.4 1-1 1A17 17 0 0 1 3 4c0-.6.4-1 1-1h3.5c.6 0 1 .4 1 1 0 1.3.2 2.5.6 3.6.1.3 0 .7-.2 1z"/></svg>(03) 9731 4052</p>
      </div>
    </div>
    <div class="appointment">
      <p class="appointment__title">Next Appointment</p>
      <p class="appointment__row">Date<span class="appointment__fill appointment__fill--date"></span>Time<span class="appointment__fill"></span></p>
      <p class="appointment__row">Date<span class="appointment__fill appointment__fill--date"></span>Time<span class="appointment__fill"></span></p>
    </div>
  </section>
</main>
</body>
</html>
```